Harbor Loom Floors Letterhead

Letterhead used for business reasons. It must be editable and easy to use.

Address is 2715 W. Pelican Lane Cedar Haven SC 34187 - 803.382.6519

```html
<!DOCTYPE html>
<html lang="en">
<head>
<meta charset="utf-8">
<title>Harbor Loom Floors Letterhead</title>
<link rel="stylesheet" href="https://fonts.googleapis.com/css2?family=Lato:wght@400;700&family=Montserrat:wght@400&family=Dancing+Script:wght@600&display=swap">
<style>
  :root {
    --backdrop: #e2e2e2;
    --paper: #ffffff;
    --brand-orange: #f07f22;
    --brand-gray: #8d8680;
    --ink: #1b1b1b;
    --contact-ink: #3a3a3a;
  }
  * { margin: 0; padding: 0; box-sizing: border-box; }
  html, body {
    width: 1174px; height: 1200px; overflow: hidden;
    background: var(--backdrop);
  }
  .letterhead {
    position: absolute; left: 138px; top: 20px;
    width: 897px; height: 1160px;
    background: var(--paper);
    font-family: "Lato", sans-serif;
    color: var(--ink);
    box-shadow: 0 2px 8px rgba(0,0,0,0.15);
  }
  .edge-band {
    position: absolute; left: 0; top: 0; bottom: 0; width: 20px;
    background: var(--brand-orange);
  }
  .edge-rule {
    position: absolute; left: 22px; top: 0; bottom: 0; width: 4px;
    background: var(--brand-gray);
  }
  .brand-name {
    position: absolute; left: 57px; top: 44px;
    font-family: "Lato", sans-serif; font-weight: 400;
    font-size: 34px; line-height: 1.15; letter-spacing: 1px;
    color: var(--brand-orange);
    display: flex; align-items: center; gap: 10px;
  }
  .brand-mark {
    width: 15px; height: 15px; background: var(--brand-orange);
  }
  .contact {
    position: absolute; right: 56px; top: 84px;
    text-align: right; font-style: normal;
    font-family: "Montserrat", sans-serif;
    font-size: 16px; line-height: 21px;
    color: var(--contact-ink);
  }
  .contact-phone {
    margin-top: 10px;
    display: flex; justify-content: flex-end; align-items: center; gap: 6px;
  }
  .contact-phone svg { width: 13px; height: 13px; }
  .letter-block {
    position: absolute; left: 57px; width: 784px;
    font-size: 17px; line-height: 20.5px;
  }
  .date { top: 286px; }
  .recipient { top: 330px; }
  .recipient-company { top: 408px; }
  .salutation { top: 510px; font-weight: 700; font-size: 21px; }
  .body-copy { top: 575px; text-align: justify; font-size: 17.5px; line-height: 19.5px; }
  .body-copy p { margin-bottom: 19px; }
  .closing { top: 927px; }
  .signature {
    position: absolute; left: 57px; top: 1000px;
    font-family: "Dancing Script", cursive; font-weight: 600;
    font-size: 38px; color: var(--ink);
  }
</style>
</head>
<body>
  <main class="letterhead">
    <div class="edge-band"></div>
    <div class="edge-rule"></div>

    <header>
      <div class="brand-name"><span class="brand-mark"></span>Harbor Loom Floors</div>
      <address class="contact">
        <div>2715 W. Pelican Lane</div>
        <div>Cedar Haven SC 34187</div>
        <div class="contact-phone">803.382.6519
          <svg viewBox="0 0 24 24" aria-hidden="true"><path fill="var(--brand-orange)" d="M6.6 10.8a15.1 15.1 0 0 0 6.6 6.6l2.2-2.2c.3-.3.7-.4 1-.2 1.1.4 2.3.6 3.6.6.6 0 1 .4 1 1V20c0 .6-.4 1-1 1A17 17 0 0 1 3 4c0-.6.4-1 1-1h3.5c.6 0 1 .4 1 1 0 1.3.2 2.5.6 3.6.1.3 0 .7-.2 1z"/></svg>
        </div>
      </address>
    </header>

    <div class="letter-block date">January-03-2020</div>
    <div class="letter-block recipient">Mr, John Doe<br>President</div>
    <div class="letter-block recipient-company">Ridgeway Holdings<br>123 Street Name, Suite# 10<br>City, State, 120023</div>
    <div class="letter-block salutation">Dear Mr, John</div>

    <div class="letter-block body-copy">
      <p>Lorem ipsum dolor sit amet, consectetur adipiscing elit, sed do eiusmod tempor incididunt ut labore et dolore magna aliqua. Ut enim ad minim veniam, quis nostrud exercitation ullamco laboris nisi ut aliquip ex ea commodo consequat. Duis aute irure dolor in reprehenderit in voluptate velit esse cillum dolore eu fugiat nulla pariatur.</p>
      <p>Lorem ipsum dolor sit amet, consectetur adipiscing elit, sed do eiusmod tempor incididunt ut labore et dolore magna aliqua. Ut enim ad minim veniam, quis nostrud exercitation ullamco laboris nisi ut aliquip ex ea commodo consequat. Duis aute irure dolor in reprehenderit in voluptate velit esse cillum dolore eu fugiat nulla pariatur.</p>
      <p>Lorem ipsum dolor sit amet, consectetur adipiscing elit, sed do eiusmod tempor incididunt ut labore et dolore magna aliqua. Ut enim ad minim veniam, quis nostrud exercitation ullamco laboris nisi ut aliquip ex ea commodo consequat.</p>
      <p>Excepteur sint occaecat cupidatat non proident, sunt in culpa qui officia deserunt mollit anim id est laborum. re et dolore magnam aliquam quaerat voluptatem.</p>
    </div>

    <div class="letter-block closing">Regards</div>
    <div class="signature">Daniel Hart</div>
  </main>
</body>
</html>
```